Qvx Brightforge Website

All the descriptions are available in the attached file. The designer has to structure the website and find the right images and icons. The website should look modern and avoid using images of real humans rather use animated images. Please note that the design should include home page, all the 4 services page , the contact us would be at the bottom of home page.

```html
<!DOCTYPE html>
<html lang="en">
<head>
<meta charset="utf-8">
<title>Qvx Brightforge</title>
<link href="https://fonts.googleapis.com/css2?family=Michroma&family=Poppins:wght@400;500;600&display=swap" rel="stylesheet">
<style>
:root{
  --blue:#2f6db5;
  --blue-dark:#2a62a6;
  --orange:#f7941d;
  --green:#5cb946;
  --grey-bg:#e7e5e8;
  --light-bg:#efeef0;
  --ink:#222;
  --text:#444;
  --white:#fff;
}
*{margin:0;padding:0;box-sizing:border-box}
html,body{width:1200px;height:3591px;overflow:hidden}
body{position:relative;background:var(--white);font-family:"Poppins",sans-serif;color:var(--text)}
.abs{position:absolute}
.display{font-family:"Michroma",sans-serif;color:var(--ink);letter-spacing:1px}
.btn{position:absolute;background:var(--blue);color:var(--white);display:flex;align-items:center;justify-content:center;font-weight:500}

/* header */
.brand{position:absolute;left:85px;top:28px;font-size:22px;font-weight:600;color:var(--blue);display:flex;align-items:center;gap:10px}
.brand .dot{width:14px;height:14px;background:var(--blue);border-radius:50%}
.nav a{position:absolute;top:48px;font-size:15px;color:#333;text-decoration:none}

/* hero */
.hero-bg{position:absolute;left:0;top:114px;width:1200px;height:583px;background:linear-gradient(90deg,#cdd4df,#dfe3ea 50%,#d9dde4)}
.hero-photo{position:absolute;left:600px;top:114px;width:600px;height:500px;background:linear-gradient(160deg,#b8c2cf,#e4e7ec 60%,#c9ced6)}
.hero-title{position:absolute;left:85px;top:196px;font-size:36px;line-height:42px}
.hero-sub{position:absolute;left:85px;top:300px;font-size:15.5px;line-height:26px;color:#333}
.dots{position:absolute;left:570px;top:502px;display:flex;gap:8px}
.dots span{width:9px;height:9px;background:rgba(255,255,255,.55)}
.dots span:first-child{background:var(--white)}

/* about */
.center{position:absolute;left:0;width:1200px;text-align:center}
.about-photo{position:absolute;left:85px;top:852px;width:530px;height:248px;background:linear-gradient(120deg,#6e5446,#c9c2bb 45%,#8a6a5a)}
.about-text{position:absolute;left:722px;top:860px;width:370px;font-size:15.5px;line-height:25.7px;color:#333}

/* services */
.services{position:absolute;left:0;top:1192px;width:1200px;height:718px;background:var(--grey-bg)}
.card{position:absolute;top:1479px;width:244px;height:264px;background:var(--white);text-align:center}
.card .icon{position:absolute;left:68px;top:-54px;width:107px;height:107px;background:var(--blue);display:flex;align-items:center;justify-content:center;box-shadow:0 0 0 3px #f4f4f6}
.card h3{position:absolute;left:0;top:85px;width:244px;font-size:19px;line-height:25px;font-weight:500;color:var(--blue)}
.card p{position:absolute;left:0;width:244px;font-size:15.5px;line-height:25.5px;color:#333}
.card .more{position:absolute;left:0;top:209px;width:228px;font-size:15px;color:var(--blue)}

/* blog */
.post{position:absolute;top:2136px;width:308px;height:401px;background:var(--white);box-shadow:0 4px 10px rgba(0,0,0,.12)}
.post .img{width:308px;height:224px}
.post .date{position:absolute;left:14px;top:268px;font-size:14px;color:#444}
.post h4{position:absolute;left:14px;top:294px;font-size:18px;font-weight:500;color:var(--ink)}
.post .tag{position:absolute;left:15px;top:338px;width:97px;height:32px;background:var(--blue);color:var(--white);font-size:12.5px;display:flex;align-items:center;justify-content:center}

/* contact */
.contact{position:absolute;left:0;top:2586px;width:1200px;height:700px;background:var(--light-bg)}
.field{position:absolute;background:var(--white);font-size:17px;color:#777;padding:0 28px;display:flex;align-items:center}
.info{position:absolute;top:3169px;display:flex;align-items:center;gap:16px;font-size:15.5px;line-height:19px;color:#333}
.info .sq{width:56px;height:56px;display:flex;align-items:center;justify-content:center;flex:none}

/* footer */
.footer-bg{position:absolute;left:0;top:3225px;width:1200px;height:366px}
.foot-brand{position:absolute;left:85px;top:3380px;font-size:34px;font-weight:600;color:var(--white);display:flex;align-items:center;gap:14px}
.foot-brand .dot{width:22px;height:22px;border-radius:50%;background:var(--white)}
.foot-nav{position:absolute;top:3405px;font-size:18px;color:var(--white)}
.foot-sep{position:absolute;top:3403px;width:2px;height:28px;background:var(--white)}
.foot-rule{position:absolute;left:85px;top:3485px;width:1030px;height:1px;background:rgba(255,255,255,.35)}
.copy{position:absolute;left:86px;top:3520px;font-size:13px;color:var(--white)}
.social{position:absolute;top:3515px;width:26px;height:26px;border:1.6px solid var(--white);border-radius:50%}
</style>
</head>
<body>

<!-- header -->
<div class="brand"><span class="dot"></span>Qvx Brightforge</div>
<nav class="nav">
  <a style="left:662px">Home</a>
  <a style="left:746px">Services <span style="color:var(--blue);font-size:11px">&#9660;</span></a>
  <a style="left:850px">Products</a>
  <a style="left:956px">Blog</a>
  <a style="left:1026px">Contact Us</a>
</nav>

<!-- hero -->
<div class="hero-bg"></div>
<div class="hero-photo" role="img" aria-label="Illustration of a consulting team working together around a laptop"></div>
<h1 class="hero-title display" style="font-weight:400">ADVANCING INNOVATION<br>THROUGH IT CONSULTING</h1>
<p class="hero-sub">Empower your digital journey with our advanced IT solutions.<br>From data to web and mobile apps, we've got you covered</p>
<div class="btn" style="left:88px;top:386px;width:194px;height:49px;font-size:18px;border:2px solid #e8eef7">Know More</div>
<div class="dots"><span></span><span></span><span></span></div>
<svg class="abs" style="left:0;top:520px" width="1200" height="200" viewBox="0 520 1200 200">
  <polygon points="0,697 860,552 1200,700 1200,720 0,720" fill="#fff"/>
  <polygon points="0,650 836,535 860,552 0,697" fill="#2f6db5"/>
  <polygon points="836,535 1200,610 1200,700 860,552" fill="#f7941d"/>
</svg>

<!-- about -->
<h2 class="center display" style="top:710px;font-size:36px">ABOUT Qvx BRIGHTFORGE</h2>
<p class="center" style="top:766px;font-size:19px;color:#333">Advancing Innovation Through IT Consulting</p>
<div class="about-photo" role="img" aria-label="Illustration of a consultant meeting clients at a table with tablets"></div>
<p class="about-text">We are a forward-thinking IT consulting firm specializing in providing cutting-edge data analytics, web application development, and mobile app development services.<br>Our passion for innovation and technology drives us to deliver tailor-made solutions</p>
<div class="btn" style="left:723px;top:1040px;width:169px;height:49px;font-size:18px">Read More</div>

<!-- services -->
<section class="services"></section>
<h2 class="center display" style="top:1300px;font-size:40px">OUR SERVICES</h2>

<div class="card" style="left:84px">
  <div class="icon"><svg width="64" height="56" viewBox="0 0 64 56" fill="none" stroke="#fff" stroke-width="4"><path d="M4 6v44h36"/><path d="M14 40V22M22 40V14"/><circle cx="40" cy="28" r="12"/><path d="M49 37l11 11"/></svg></div>
  <h3>Data Analytics</h3>
  <p style="top:115px">Lorem ipsum dolor sit amet,<br>consec tetur adipiscing elit<br>Lorem ipsum dolor sit amet</p>
  <div class="more">Read More...</div>
</div>
<div class="card" style="left:347px">
  <div class="icon"><svg width="64" height="56" viewBox="0 0 64 56" fill="none" stroke="#fff" stroke-width="4"><rect x="4" y="6" width="56" height="36"/><path d="M24 50h16M32 42v8"/><path d="M18 30l8-8-8-8M34 32h12"/></svg></div>
  <h3>Web Development</h3>
  <p style="top:115px">Lorem ipsum dolor sit amet,<br>consec tetur adipiscing elit<br>Lorem ipsum dolor sit amet</p>
  <div class="more">Read More...</div>
</div>
<div class="card" style="left:611px">
  <div class="icon"><svg width="40" height="60" viewBox="0 0 40 60" fill="none" stroke="#fff" stroke-width="4"><rect x="6" y="4" width="28" height="52" rx="4"/><path d="M16 48h8"/></svg></div>
  <h3>Mobile App<br>Development</h3>
  <p style="top:140px">Lorem ipsum dolor sit amet,<br>consec tetur adipiscing elit</p>
  <div class="more">Read More...</div>
</div>
<div class="card" style="left:873px">
  <div class="icon"><svg width="48" height="62" viewBox="0 0 48 62" fill="#fff"><path d="M24 2c10 10 12 24 8 40H16C12 26 14 12 24 2z"/><path d="M14 30l-10 16 10-2zM34 30l10 16-10-2z"/><circle cx="24" cy="22" r="5" fill="#2f6db5"/><path d="M18 46h12l-6 12z"/></svg></div>
  <h3>Start-up Partner</h3>
  <p style="top:115px">Lorem ipsum dolor sit amet,<br>consec tetur adipiscing elit<br>Lorem ipsum dolor sit amet</p>
  <div class="more">Read More...</div>
</div>

<!-- blog -->
<h2 class="center display" style="top:2002px;font-size:40px">LATEST BLOG</h2>
<article class="post" style="left:85px">
  <div class="img" role="img" aria-label="Illustration of a business meeting in a bright office" style="background:linear-gradient(135deg,#9aa09c,#d6d8d4 50%,#7c7f80)"></div>
  <div class="date">2 APRIL 2023</div>
  <h4>Lorem ipsum dolor sit amet</h4>
  <div class="tag">Read More</div>
</article>
<article class="post" style="left:443px">
  <div class="img" role="img" aria-label="Illustration of a team gathered around a laptop" style="background:linear-gradient(135deg,#5a5a5c,#cfcbc6 50%,#3e3e40)"></div>
  <div class="date">20 APRIL 2023</div>
  <h4>Sit ametconsect etuadip...</h4>
  <div class="tag">Read More</div>
</article>
<article class="post" style="left:803px">
  <div class="img" role="img" aria-label="Illustration of colleagues joining hands over a wooden table" style="background:linear-gradient(135deg,#a9a39c,#6f4a36 50%,#8b6a54)"></div>
  <div class="date">22 APRIL 2023</div>
  <h4>Lorem ipsum dolor sit amet</h4>
  <div class="tag">Read More</div>
</article>

<!-- contact -->
<section class="contact"></section>
<div class="abs" style="left:6px;top:2586px;width:1158px;height:56px;background:var(--white)"></div>
<h2 class="center display" style="top:2718px;font-size:40px">CONTACT US</h2>
<div class="field" style="left:85px;top:2834px;width:411px;height:73px">First Name*</div>
<div class="field" style="left:514px;top:2834px;width:292px;height:73px">Phone Number*</div>
<div class="field" style="left:824px;top:2834px;width:291px;height:73px">Email Address*</div>
<div class="field" style="left:85px;top:2929px;width:1030px;height:92px;align-items:flex-start;padding:30px 21px">Message*</div>
<div class="btn" style="left:521px;top:3042px;width:179px;height:61px;font-size:18px;font-weight:400">Submit</div>

<div class="info" style="left:85px">
  <div class="sq" style="background:var(--blue)"><svg width="22" height="30" viewBox="0 0 22 30"><path d="M11 1C5 1 1 5.5 1 11c0 7 10 18 10 18s10-11 10-18C21 5.5 17 1 11 1z" fill="#fff"/><circle cx="11" cy="11" r="4" fill="#2f6db5"/></svg></div>
  <span>Suite 12/40 Harbour Lane,<br>Eastvale WA 6020</span>
</div>
<div class="info" style="left:427px">
  <div class="sq" style="background:var(--orange)"><svg width="28" height="28" viewBox="0 0 24 24"><path d="M6.6 10.8a15 15 0 0 0 6.6 6.6l2.2-2.2c.3-.3.7-.4 1-.2 1.1.4 2.3.6 3.6.6.6 0 1 .4 1 1V20c0 .6-.4 1-1 1A17 17 0 0 1 3 4c0-.6.4-1 1-1h3.5c.6 0 1 .4 1 1 0 1.3.2 2.5.6 3.6.1.3 0 .7-.2 1z" fill="#fff"/></svg></div>
  <span>+61 (08) 5550 0142 (Sales / Support)</span>
</div>
<div class="info" style="left:801px">
  <div class="sq" style="background:var(--green)"><svg width="30" height="22" viewBox="0 0 30 22" fill="none" stroke="#fff" stroke-width="2.5"><rect x="2" y="2" width="26" height="18"/><path d="M2 2l13 10L28 2"/></svg></div>
  <span>hello@qvxbrightforge.example</span>
</div>

<!-- footer -->
<svg class="footer-bg" width="1200" height="366" viewBox="0 3225 1200 366">
  <polygon points="0,3248 862,3376 1200,3225 1200,3591 0,3591" fill="#2f6db5"/>
  <polygon points="0,3248 862,3376 0,3276" fill="#5cb946"/>
  <polygon points="862,3376 1200,3225 1200,3238" fill="#f7941d"/>
</svg>
<div class="foot-brand"><span class="dot"></span>Qvx Brightforge</div>
<div class="foot-nav" style="left:605px">Home</div>
<div class="foot-sep" style="left:677px"></div>
<div class="foot-nav" style="left:697px">Services</div>
<div class="foot-sep" style="left:791px"></div>
<div class="foot-nav" style="left:818px">Products</div>
<div class="foot-sep" style="left:914px"></div>
<div class="foot-nav" style="left:934px">Blog</div>
<div class="foot-sep" style="left:993px"></div>
<div class="foot-nav" style="left:1013px">Contact us</div>
<div class="foot-rule"></div>
<div class="copy">Copyright @ &nbsp;2023 All rights reserved</div>
<div class="social" style="left:946px"></div>
<div class="social" style="left:991px"></div>
<div class="social" style="left:1037px"></div>
<div class="social" style="left:1085px"></div>

</body>
</html>
```